Business cards - BRENT Roofing & Siding

We need simple business cards made up for our Roofing & Siding business based in Calgary Alberta.
The logo on one side of the card and potentially our slogan "Built with trust, verified by time".
The other side could have:
-A small logo
-Rep name:
-Rep cell phone:
-Rep email:
-Office phone: 403-684-2093
-Website: PrairieShingleWorks.com

We would like to incorporate the colours from our logo, especially the lite blue on the jpeg file. I have attached the ai file and jpeg file. We like the colours better on the jpeg file.

I do not require a money back guarantee

```html
<!DOCTYPE html>
<html lang="en">
<head>
<meta charset="utf-8">
<title>BRENT Roofing &amp; Siding – Business Cards</title>
<link href="https://fonts.googleapis.com/css2?family=Exo+2:ital,wght@0,300;0,400;0,600;0,700;0,800;1,300&display=swap" rel="stylesheet">
<style>
  :root{
    --stage:#2b2b2e;
    --white:#ffffff;
    --ink:#141414;
    --grey:#3a3a3a;
    --navy-blue:#0068b5;
    --sky-blue:#0a8ce8;
    --maple-red:#e8202a;
  }
  *{margin:0;padding:0;box-sizing:border-box}
  html,body{width:1200px;height:718px;overflow:hidden}
  body{background:var(--stage);font-family:"Exo 2",sans-serif;position:relative}
  .card{position:absolute;top:205px;width:540px;height:309px;border-radius:16px;overflow:hidden;box-shadow:0 14px 30px rgba(0,0,0,.45)}
  .card svg.art{position:absolute;inset:0}
  .card--front{left:40px;background:var(--white)}
  .card--back{left:620px;background:var(--sky-blue)}

  .brand{position:absolute;left:34px;top:52px}
  .brand__est{font-size:12px;font-weight:400;color:var(--ink);letter-spacing:1px;margin-left:50px;margin-bottom:2px}
  .brand__name{font-size:26px;font-weight:600;color:var(--ink);letter-spacing:2px;line-height:1.1}
  .brand__name small{display:block;font-size:16px;letter-spacing:3px}

  .slogan{position:absolute;right:40px;bottom:28px;text-align:right;font-size:19px;line-height:1.15;text-transform:uppercase}
  .slogan__trust{color:var(--sky-blue);font-weight:300}
  .slogan__trust b{font-weight:800}
  .slogan__time{color:var(--maple-red);font-weight:300}
  .slogan__time b{font-weight:800}

  .rep{position:absolute;right:34px;top:46px;text-align:right;color:var(--white)}
  .rep__name{font-size:30px;font-weight:800;letter-spacing:.5px;line-height:1}
  .rep__title{font-size:17px;font-weight:400;margin-bottom:14px}
  .rep__line{display:flex;justify-content:flex-end;align-items:center;gap:8px;font-size:14px;line-height:1.45;white-space:nowrap}
  .rep__line svg{width:12px;height:12px;flex:none}
</style>
</head>
<body>

<section class="card card--front" aria-label="Card front">
  <svg class="art" width="540" height="309" viewBox="0 0 540 309">
    <polygon points="455,0 495,0 540,95 540,150" fill="var(--sky-blue)"/>
    <polygon points="115,309 215,309 468,146 440,80" fill="var(--navy-blue)"/>
  </svg>
  <div class="brand">
    <p class="brand__est">Est. 1991</p>
    <p class="brand__name">BRENT<small>Roofing &amp; Siding</small></p>
  </div>
  <div class="slogan">
    <p class="slogan__trust">Built <b>with trust</b></p>
    <p class="slogan__time">Verified <b>by time</b></p>
  </div>
</section>

<section class="card card--back" aria-label="Card back">
  <svg class="art" width="540" height="309" viewBox="0 0 540 309">
    <polygon points="0,95 0,309 175,309" fill="var(--white)"/>
    <polygon points="40,0 78,0 340,309 300,309" fill="var(--white)"/>
    <rect x="158" y="140" width="102" height="150" rx="6" fill="var(--maple-red)" role="img" aria-label="Large red maple leaf emblem"/>
  </svg>
  <div class="rep">
    <p class="rep__name">DALE WHITMORE</p>
    <p class="rep__title">Managing Director</p>
    <p class="rep__line">403-684-2093
      <svg viewBox="0 0 12 12"><path d="M2.5 1h2l1 3-1.3 1a6 6 0 0 0 2.8 2.8l1-1.3 3 1v2c0 .6-.5 1-1 1A9.5 9.5 0 0 1 1.5 2c0-.5.4-1 1-1z" fill="var(--white)"/></svg></p>
    <p class="rep__line">403-684-2093
      <svg viewBox="0 0 12 12"><rect x="3" y="0.5" width="6" height="11" rx="1.2" fill="none" stroke="var(--white)" stroke-width="1.3"/><circle cx="6" cy="9.5" r=".8" fill="var(--white)"/></svg></p>
    <p class="rep__line">dale@prairieshingleworks.com
      <svg viewBox="0 0 12 12"><rect x="0.5" y="2" width="11" height="8" fill="var(--white)"/><path d="M0.5 2 6 6.5 11.5 2" fill="none" stroke="var(--sky-blue)" stroke-width="1"/></svg></p>
    <p class="rep__line">PrairieShingleWorks.com
      <svg viewBox="0 0 12 12"><circle cx="6" cy="6" r="5.2" fill="none" stroke="var(--white)" stroke-width="1.3"/><path d="M1 6h10M6 1c-2.5 3-2.5 7 0 10M6 1c2.5 3 2.5 7 0 10" fill="none" stroke="var(--white)" stroke-width="1"/></svg></p>
  </div>
</section>

</body>
</html>
```